Life and Personal development life coach needs card design

I need a card design that matches the style and design of my website. I'd like to stay in the same color scheme. Please check out my website for ideas. www.loretabrenvik.com
I have had previous designs for this. I am wondering if you have access to those for more ideas??

```html
<!DOCTYPE html>
<html lang="en">
<head>
<meta charset="utf-8">
<title>Loreta Brenvik – Life Coach Business Card</title>
<link href="https://fonts.googleapis.com/css2?family=Montserrat:wght@400;600;700;800&display=swap" rel="stylesheet">
<style>
  :root {
    --lime: #a8d311;
    --lime-dark: #8fb80a;
    --ink: #1d1d1b;
    --grey: #5c5c5c;
    --paper: #ffffff;
    --backdrop: #ecebe8;
  }
  * { box-sizing: border-box; margin: 0; padding: 0; }
  html, body {
    width: 1200px; height: 435px; overflow: hidden;
    background: var(--backdrop);
  }
  .stage { position: relative; width: 1200px; height: 435px; }

  .card {
    position: absolute; top: 72px;
    width: 510px; height: 291px;
    background: var(--paper);
    border-radius: 16px;
    overflow: hidden;
    box-shadow: 0 2px 6px rgba(0,0,0,0.12);
  }

  /* ---------- Front ---------- */
  .card--front { left: 50px; text-align: center; }
  .brand {
    display: flex; align-items: center; justify-content: center; gap: 14px;
    margin-top: 62px;
  }
  .brand__dot {
    width: 26px; height: 26px; border-radius: 50%; background: var(--lime);
  }
  .brand__name {
    font-family: "Montserrat", sans-serif; font-weight: 600;
    font-size: 40px; letter-spacing: 1px; color: var(--grey);
  }
  .front__tagline {
    font-family: "Montserrat", sans-serif; font-weight: 600;
    font-size: 11px; color: var(--grey); margin-top: 12px;
  }
  .front__motto {
    font-family: "Montserrat", sans-serif; font-weight: 600;
    font-size: 20px; color: var(--lime-dark); margin-top: 8px;
  }
  .front__web {
    display: inline-block; margin-top: 22px;
    background: var(--lime); color: var(--ink);
    font-family: "Montserrat", sans-serif; font-weight: 800;
    font-size: 21px; padding: 6px 28px; border-radius: 22px;
  }

  /* ---------- Back ---------- */
  .card--back { left: 640px; }
  .back__band {
    background: var(--lime); height: 62px; text-align: center;
    padding-top: 11px; color: var(--ink);
  }
  .back__heading {
    font-family: "Montserrat", sans-serif; font-weight: 800; font-size: 15.5px;
  }
  .back__subheading {
    font-family: "Montserrat", sans-serif; font-weight: 400; font-size: 14px;
    margin-top: 3px;
  }
  .back__name {
    position: absolute; left: 200px; top: 78px;
    font-family: "Montserrat", sans-serif; font-weight: 800;
    font-size: 25px; color: var(--lime); white-space: nowrap;
  }
  .pill {
    position: absolute; background: var(--lime); color: var(--ink);
    font-family: "Montserrat", sans-serif; border-radius: 14px; white-space: nowrap;
  }
  .back__role { left: 195px; top: 112px; font-size: 14px; font-weight: 700; padding: 3px 14px; }
  .back__phone { left: 44px; top: 108px; font-size: 15px; font-weight: 700; padding: 4px 14px; }
  .back__email { left: 252px; top: 150px; font-size: 15px; font-weight: 700; padding: 4px 14px; }
  .back__hours-label { left: 14px; top: 150px; font-size: 10px; font-weight: 800; padding: 5px 10px; }
  .icon { position: absolute; }
  .icon--phone { left: 20px; top: 110px; }
  .icon--mail { left: 218px; top: 154px; }

  .hours {
    position: absolute; font-family: "Montserrat", sans-serif; font-weight: 800;
    font-size: 12px; line-height: 1.45; color: var(--lime); text-align: center; white-space: nowrap;
  }
  .hours--weekdays { left: 118px; top: 190px; }
  .hours--friday { left: 248px; top: 214px; }
  .hours--weekend { left: 378px; top: 236px; }
  .back__footer {
    position: absolute; left: 0; right: 0; bottom: 0; height: 8px; background: var(--lime);
  }
</style>
</head>
<body>
<main class="stage">

  <section class="card card--front" aria-label="Card front">
    <div class="brand">
      <span class="brand__dot" aria-hidden="true"></span>
      <h1 class="brand__name">Loreta Brenvik</h1>
    </div>
    <p class="front__tagline">Health, Strength &amp; Balance for Your Mind and Soul</p>
    <p class="front__motto">Discover a life without limits!</p>
    <span class="front__web">www.loretabrenvik.com</span>
  </section>

  <section class="card card--back" aria-label="Card back">
    <header class="back__band">
      <p class="back__heading">LIFE AND PERSONAL DEVELOPMENT LIFE COACH</p>
      <p class="back__subheading">Discover a life without limits!</p>
    </header>

    <h2 class="back__name">LORETA BRENVIK, RN</h2>
    <span class="pill back__role">TRANSFORMATIONAL LIFE COACH</span>

    <svg class="icon icon--phone" width="16" height="24" viewBox="0 0 16 24" aria-hidden="true">
      <rect x="1.5" y="1.5" width="13" height="21" rx="2" fill="none" stroke="var(--lime)" stroke-width="2"/>
      <line x1="6" y1="19" x2="10" y2="19" stroke="var(--lime)" stroke-width="1.5"/>
    </svg>
    <span class="pill back__phone">619-555-0148</span>

    <svg class="icon icon--mail" width="24" height="16" viewBox="0 0 24 16" aria-hidden="true">
      <rect x="0" y="0" width="24" height="16" rx="1" fill="var(--lime)"/>
      <polyline points="1,1 12,9 23,1" fill="none" stroke="var(--paper)" stroke-width="1.6"/>
    </svg>
    <span class="pill back__email">loreta@loretabrenvik.com</span>

    <span class="pill back__hours-label">COACHING HOURS</span>
    <p class="hours hours--weekdays">MONDAY - THURSDAY<br>9:00AM - 8:00PM</p>
    <p class="hours hours--friday">FRIDAY<br>9:00AM - 6:00PM</p>
    <p class="hours hours--weekend">SAT - SUNDAY<br>9:00AM - 4:00PM</p>

    <div class="back__footer"></div>
  </section>

</main>
</body>
</html>
```